Business Card Design For Financial Company

Create a new design for company's business card. The corporate logo is attached in several formats. Our new website design is also attached and we would like the business cards to reflect this.
Card needs to contain the following info:
Name
Job Title
Legal company name - eg Varo-Q Capital (Asia) Ltd
Address - eg 612-09 Belmore Plaza,47 Tamsin Street, Hong Kong
Direct tel
Main tel
Fax
Email
Website URL
MS word format preferred. Other formats that can be edited on standard PC also OK.
Updates
Please note the the "VARO-Q" logo nameĀ font is "Gill Sans MT" on Windows
Target Market(s)
Instituation Investors
Industry/Entity Type
Business
Look and feel

```html
<!DOCTYPE html>
<html lang="en">
<head>
<meta charset="utf-8">
<title>Varo-Q Capital – Business Card</title>
<link rel="stylesheet" href="https://fonts.googleapis.com/css2?family=Cabin:wght@400;500&display=swap">
<style>
  :root {
    --backdrop: #98a2a8;
    --card-white: #ffffff;
    --brand-red: #d20f1e;
    --ink: #1a1a1a;
    --on-red: #ffffff;
  }
  * { margin: 0; padding: 0; box-sizing: border-box; }
  html, body {
    width: 1200px;
    height: 900px;
    overflow: hidden;
    background: var(--backdrop);
    font-family: "Cabin", "Gill Sans", sans-serif;
  }
  .canvas { position: relative; width: 1200px; height: 900px; }

  .card { position: absolute; left: 335px; width: 606px; height: 369px; }
  .card--front { top: 60px; background: var(--card-white); }
  .card--back { top: 459px; background: var(--brand-red); color: var(--on-red); }

  .brand-name {
    position: absolute; left: 40px; top: 214px;
    font-size: 42px; font-weight: 400; color: var(--ink);
    letter-spacing: 1px; line-height: 1;
  }

  .tagline-band {
    position: absolute; left: 302px; top: 201px;
    width: 304px; height: 67px;
    background: var(--brand-red); color: var(--on-red);
    padding: 9px 0 0 20px;
    font-size: 20px; line-height: 25px; text-transform: uppercase;
  }

  .contact { position: absolute; left: 41px; top: 34px; font-size: 19px; line-height: 26px; font-weight: 400; }
  .contact__name { font-weight: 500; }
  .contact__group { margin-top: 10px; }

  .back-label {
    position: absolute; left: 448px; top: 223px;
    width: 158px; height: 46px;
    background: var(--card-white);
    padding-left: 12px;
    display: flex; align-items: center;
  }
  .back-label__name { font-size: 31px; color: var(--ink); letter-spacing: 1px; }
</style>
</head>
<body>
<main class="canvas">
  <section class="card card--front">
    <span class="brand-name">VARO-Q</span>
    <div class="tagline-band">
      <p>Independent Research</p>
      <p>Marketing &amp; Execution</p>
    </div>
  </section>

  <section class="card card--back">
    <div class="contact">
      <p class="contact__name">Daniel Hart</p>
      <p class="contact__title">Sales Manager</p>
      <div class="contact__group">
        <p>Varo-Q Capital (Asia) Ltd</p>
        <p>612-09 Belmore Plaza</p>
        <p>47 Tamsin Street</p>
        <p>Hong Kong</p>
      </div>
      <div class="contact__group">
        <p>main tel: 318 402 7765</p>
        <p>direct tel: 447 290 3185</p>
        <p>fax: 018 563 2094</p>
        <p>e-mail: contact@varoqcapital.com</p>
        <p>url: www.varoqcapital.com</p>
      </div>
    </div>
    <div class="back-label">
      <span class="back-label__name">VARO-Q</span>
    </div>
  </section>
</main>
</body>
</html>
```